Business Card and Letterhead for Pimlu - modern real estate business

I need a double sided business card design for Pimlu. Please see business card brief here https://files.trelvonadocs.com/sheet/r/7QzTmWbaXLJnoPEd-kRyUgFhHsstbvCe2qfoMxDa_pz/view?mode=shared

Please feel free to design the business cards however you feel best. I am happy to give some creative freedoms and then provide feedback from there.

Please then also create a letterhead to match the business card design

Colors

Designer to choose colors to be used in the design.

Requirements
Must have
• Must be a modern, elegant business card which looks very professional

```html
<!DOCTYPE html>
<html lang="en">
<head>
<meta charset="utf-8">
<title>Pimlu – Letterhead and Business Card</title>
<link rel="stylesheet" href="https://fonts.googleapis.com/css2?family=Exo+2:wght@700&family=Open+Sans:wght@400;500&display=swap">
<style>
  :root {
    --backdrop: #a3b6bc;
    --paper: #ffffff;
    --brand-red: #e3131b;
    --ink: #2b2b2b;
    --ink-soft: #4a4a4a;
    --rule: #8a8a8a;
    --photo-dark: #3a3a3c;
    --photo-light: #8c8c8e;
    --shadow: 0 2px 5px rgba(0,0,0,0.25);
    --brand-font: "Exo 2", sans-serif;
    --text-font: "Open Sans", sans-serif;
  }
  * { margin: 0; padding: 0; box-sizing: border-box; }
  html, body { width: 1200px; height: 900px; overflow: hidden; }
  body { background: var(--backdrop); position: relative; font-family: var(--text-font); color: var(--ink); }

  .sheet { position: absolute; background: var(--paper); box-shadow: var(--shadow); }

  .wordmark { font-family: var(--brand-font); font-weight: 700; color: var(--brand-red); letter-spacing: 1px; line-height: 1; position: absolute; white-space: nowrap; }

  /* Letterhead */
  .letterhead { left: 109px; top: 86px; width: 570px; height: 727px; }
  .letterhead .wordmark { font-size: 32px; left: 0; right: 0; top: 14px; text-align: center; }
  .letter-date { position: absolute; left: 63px; top: 203px; font-size: 9.5px; color: var(--ink-soft); }
  .letter-body { position: absolute; left: 63px; top: 246px; width: 445px; font-size: 9.3px; line-height: 20.5px; color: var(--ink-soft); }
  .letter-body p { margin-bottom: 3px; white-space: nowrap; overflow: hidden; }
  .signature-mark { position: absolute; left: 392px; top: 510px; width: 110px; height: 34px; background: linear-gradient(90deg, #f1f1f1, #fafafa); border-radius: 4px; }
  .signatory { position: absolute; left: 397px; top: 546px; font-size: 8.5px; line-height: 11px; color: var(--ink-soft); }
  .letter-footer { position: absolute; left: 44px; top: 676px; width: 482px; text-align: center; }
  .footer-rule { position: relative; height: 16px; }
  .footer-rule::before { content: ""; position: absolute; left: 0; right: 0; top: 8px; border-top: 1px solid var(--rule); }
  .footer-rule .icon-row { position: relative; background: var(--paper); padding: 0 2px; }
  .footer-contacts { font-size: 9.5px; line-height: 14px; color: var(--ink); }
  .footer-contacts span + span { margin-left: 10px; }

  .icon-row { display: inline-flex; gap: 2px; }
  .icon-row svg { width: 11px; height: 11px; display: block; }

  /* Business card front */
  .card-front { left: 710px; top: 346px; width: 381px; height: 217px; overflow: hidden; }
  .agent-photo { position: absolute; left: 0; top: 0; width: 175px; height: 217px; background: linear-gradient(180deg, var(--photo-light) 0%, var(--photo-dark) 70%); }
  .card-front .wordmark { font-size: 38px; left: 180px; width: 183px; top: 26px; text-align: center; }
  .agent-details { position: absolute; left: 185px; width: 175px; top: 85px; text-align: center; }
  .agent-name { font-family: var(--brand-font); font-weight: 700; color: var(--brand-red); font-size: 17px; letter-spacing: 0.5px; line-height: 20px; }
  .agent-role { font-size: 10.5px; color: var(--ink); line-height: 14px; }
  .card-icons { position: relative; height: 14px; margin: 12px auto 2px; width: 88px; }
  .card-icons::before { content: ""; position: absolute; left: 0; right: 0; top: 7px; border-top: 1px solid var(--rule); }
  .card-icons .icon-row { position: relative; background: var(--paper); padding: 0 2px; }
  .card-icons .icon-row svg { width: 13px; height: 13px; }
  .agent-contacts { font-size: 11px; line-height: 13px; color: var(--ink); }
  .card-front .address-rule { position: absolute; left: 175px; right: 0; top: 193px; border-top: 1px solid #9a9a9a; }
  .address-band { position: absolute; left: 175px; right: 0; top: 198px; height: 19px; background: var(--brand-red); color: #fff; font-size: 10.5px; line-height: 19px; padding-left: 16px; }

  /* Business card back */
  .card-back { left: 710px; top: 597px; width: 381px; height: 216px; }
  .card-back .wordmark { font-size: 50px; left: 0; right: 0; top: 83px; text-align: center; }
</style>
</head>
<body>

<svg width="0" height="0" style="position:absolute" aria-hidden="true">
  <defs>
    <symbol id="icon-phone" viewBox="0 0 20 20">
      <circle cx="10" cy="10" r="10" fill="#e3131b"/>
      <path d="M6.2 5.2l1.8-.4 1 2.4-1.1.8c.6 1.3 1.5 2.2 2.8 2.8l.8-1.1 2.4 1-.4 1.8c-3.8.2-7.5-3.5-7.3-7.3z" fill="#fff"/>
    </symbol>
    <symbol id="icon-mail" viewBox="0 0 20 20">
      <circle cx="10" cy="10" r="10" fill="#e3131b"/>
      <rect x="5" y="6.5" width="10" height="7" rx="0.8" fill="#fff"/>
      <path d="M5.3 7l4.7 3.6L14.7 7" fill="none" stroke="#e3131b" stroke-width="1"/>
    </symbol>
    <symbol id="icon-web" viewBox="0 0 20 20">
      <circle cx="10" cy="10" r="10" fill="#e3131b"/>
      <circle cx="10" cy="10" r="5" fill="none" stroke="#fff" stroke-width="1.2"/>
      <ellipse cx="10" cy="10" rx="2.2" ry="5" fill="none" stroke="#fff" stroke-width="1"/>
      <path d="M5 10h10" stroke="#fff" stroke-width="1"/>
    </symbol>
  </defs>
</svg>

<section class="sheet letterhead" aria-label="Letterhead">
  <div class="wordmark">PIMLU</div>
  <p class="letter-date">Date, 10 September, 2020</p>
  <div class="letter-body">
    <p>This is a sample letter that has been placed to demonstrate typing remat (Your Company). letterhead<br>design. When positioned properly, it will serve to work in harmony with all other elements letterhead.<br>This letterhead design is meant to project an image</p>
    <p>This letterhead design is meant project an image of professionalism reliability. By using simple aligen<br>we have created a very spacious feeling. The simplicity suggest  rengththe spaciousnes contributes h<br>aesthetics the layout. These basic qualities along with the (Your Company)</p>
    <p>look and helps reinforce the (Your Company) brand. letterhead design is meant to project an image p<br>design. When positioned properly, it will serve to work in harmony all the other elements letterhead.<br>sionalism and reliability.</p>
    <p>This letterhead design is based on the (Form of your logo) form (Your Company) logo. Each stationery<br>we have created a very spacious feeling. The simplicity suggests strength the spaciousnes contribute<br>part of the (Form of your logo).</p>
  </div>
  <div class="signature-mark" role="img" aria-label="Handwritten signature of Ellis Marrow"></div>
  <p class="signatory">Ellis Marrow<br>Manager</p>
  <footer class="letter-footer">
    <div class="footer-rule">
      <span class="icon-row">
        <svg><use href="#icon-phone"/></svg><svg><use href="#icon-mail"/></svg><svg><use href="#icon-web"/></svg>
      </span>
    </div>
    <p class="footer-contacts"><span>0400 555 218</span><span>rowan@pimlu.com</span><span>www.pimlu.com</span></p>
    <p class="footer-contacts">PO Box 1180, Fernbrook NSW 2790</p>
  </footer>
</section>

<section class="sheet card-front" aria-label="Business card, front">
  <div class="agent-photo" role="img" aria-label="Portrait photo of the agent in a dark suit"></div>
  <div class="wordmark">PIMLU</div>
  <div class="agent-details">
    <p class="agent-name">ROWAN PELLIER</p>
    <p class="agent-role">Licenced Real Estate Agent</p>
    <div class="card-icons">
      <span class="icon-row">
        <svg><use href="#icon-phone"/></svg><svg><use href="#icon-mail"/></svg><svg><use href="#icon-web"/></svg>
      </span>
    </div>
    <p class="agent-contacts">0400 555 218<br>rowan@pimlu.com<br>www.pimlu.com</p>
  </div>
  <div class="address-rule"></div>
  <div class="address-band">PO Box 1180, Fernbrook NSW 2790</div>
</section>

<section class="sheet card-back" aria-label="Business card, back">
  <div class="wordmark">PIMLU</div>
</section>

</body>
</html>
```